Business Cards - New Logo Rebranding

Hello We know have a red and blue logo and are looking to create new cards. We are looking for the best creativity of the new logo merged with some of the existing artwork provided.

Target Market(s)

Realtors

Industry/Entity Type

Real Estate

Contact Information for Business Card

New logo with rebranded colors

Requirements
Must have
• Creative use of the new logo

```html
<!DOCTYPE html>
<html lang="en">
<head>
<meta charset="utf-8">
<title>Summit Crest Business Cards</title>
<link href="https://fonts.googleapis.com/css2?family=Arimo:wght@400;700&display=swap" rel="stylesheet">
<style>
  :root {
    --stage: #3c3c3c;
    --card-dark: #2d2d2e;
    --card-light: #ffffff;
    --brand-red: #e0262e;
    --brand-blue: #1b6fc4;
    --ink-white: #ffffff;
    --ink-grey: #4a4a4a;
    --emboss: #3a3a3b;
  }
  * { box-sizing: border-box; margin: 0; padding: 0; }
  html, body { width: 1200px; height: 803px; overflow: hidden; }
  body {
    background: var(--stage);
    font-family: "Arimo", Arial, sans-serif;
    position: relative;
  }
  .card {
    position: absolute;
    top: 250px;
    width: 520px;
    height: 300px;
    border-radius: 22px;
    border-bottom: 4px solid var(--brand-red);
    overflow: hidden;
  }
  .card--back { left: 55px; background: var(--card-dark); }
  .card--front { left: 625px; background: var(--card-light); }

  .emboss-circle {
    position: absolute;
    right: 40px; top: 30px;
    width: 200px; height: 200px;
    border-radius: 50%;
    border: 6px solid var(--emboss);
    background: #333334;
  }
  .back-brand {
    position: absolute; left: 34px; top: 70px;
  }
  .wordmark {
    font-weight: 700;
    font-size: 30px;
    letter-spacing: 1px;
    text-transform: uppercase;
    line-height: 1;
  }
  .back-brand .wordmark { color: var(--ink-white); }
  .tagline {
    font-size: 9px; font-weight: 700; letter-spacing: 0.6px;
    text-transform: uppercase; margin-top: 5px;
  }
  .back-brand .tagline { color: var(--ink-white); border-top: 1px solid var(--ink-white); padding-top: 4px; display: inline-block; }

  .person { position: absolute; left: 34px; top: 152px; }
  .person-name { color: var(--brand-blue); font-size: 22px; }
  .person-title { color: var(--brand-red); font-size: 12px; margin-top: 2px; }

  .contact-list { position: absolute; left: 34px; top: 212px; list-style: none; }
  .contact-list li {
    display: flex; align-items: center; gap: 9px;
    color: var(--ink-white); font-size: 12px; line-height: 17px;
  }
  .contact-list svg { width: 11px; height: 11px; fill: none; stroke: var(--brand-blue); stroke-width: 2; }

  .front-logo { position: absolute; left: 0; right: 0; top: 40px; text-align: center; }
  .front-logo .badge {
    width: 110px; height: 110px; border-radius: 50%;
    border: 5px solid var(--brand-red); margin: 0 auto 14px;
  }
  .front-logo .wordmark { color: var(--brand-blue); font-size: 34px; }
  .front-logo .tagline { color: var(--brand-blue); }
  .services {
    position: absolute; left: 0; right: 0; bottom: 38px;
    text-align: center; color: var(--ink-grey);
    font-size: 15px; letter-spacing: 0.4px;
  }
</style>
</head>
<body>
  <section class="card card--back">
    <div class="emboss-circle"></div>
    <div class="back-brand">
      <div class="wordmark">Summit Crest</div>
      <div class="tagline">Inspection Professionals</div>
    </div>
    <div class="person">
      <div class="person-name">Dana Moreland</div>
      <div class="person-title">Certified Mold Inspector</div>
    </div>
    <ul class="contact-list">
      <li><svg viewBox="0 0 12 12"><path d="M2 1 L4 1 L5 4 L3.5 5 Q5 8 7 8.5 L8 7 L11 8 L11 10 Q6 11 2 6 Q1 3 2 1Z"/></svg>800.555.0142</li>
      <li><svg viewBox="0 0 12 12"><rect x="3" y="1" width="6" height="10" rx="1"/></svg>562.555.0187</li>
      <li><svg viewBox="0 0 12 12"><rect x="1" y="2.5" width="10" height="7"/><path d="M1 2.5 L6 7 L11 2.5"/></svg>dana@summitcrestinspect.com</li>
      <li><svg viewBox="0 0 12 12"><circle cx="6" cy="6" r="5"/><path d="M1 6 H11 M6 1 Q3 6 6 11 Q9 6 6 1"/></svg>www.SummitCrestInspect.com</li>
    </ul>
  </section>

  <section class="card card--front">
    <div class="front-logo">
      <div class="badge"></div>
      <div class="wordmark">Summit Crest</div>
      <div class="tagline">Inspection Professionals</div>
    </div>
    <p class="services">HOME • SEWER • MOLD • COMMERCIAL • TERMITE • ROOF</p>
  </section>
</body>
</html>
```